Veldmark Supplies Business Card

Professional business card that stand out to our potential customers. Front and back with clean modern design

Industry/Entity Type

Oil and gas

Contact Information for Business Card

Name, address, website , office phone and cell number

Requirements
Must have
• Editable files for each employee

```html
<!DOCTYPE html>
<html lang="en">
<head>
<meta charset="utf-8">
<title>Veldmark Supplies Business Card</title>
<link href="https://fonts.googleapis.com/css2?family=Poppins:wght@400;600;700&display=swap" rel="stylesheet">
<style>
  :root {
    --brand-red: #e8262a;
    --brand-cyan: #16afd0;
    --ink: #1d1d1f;
    --paper: #ffffff;
    --backdrop: #e3e7e9;
    --foil: #f7cdb8;
  }
  * { margin: 0; padding: 0; box-sizing: border-box; }
  html, body { width: 1200px; height: 960px; overflow: hidden; }
  body {
    background: var(--backdrop);
    font-family: "Poppins", sans-serif;
    position: relative;
  }
  .card {
    position: absolute;
    left: 249px;
    width: 702px;
    height: 400px;
    overflow: hidden;
  }
  .card-front { top: 73px; background: var(--brand-red); }
  .card-back { top: 513px; background: var(--paper); }

  .brand-lockup {
    position: absolute;
    left: 0; right: 0;
    display: flex;
    align-items: center;
    justify-content: center;
    gap: 14px;
    font-weight: 700;
    text-transform: uppercase;
    letter-spacing: 0.06em;
  }
  .brand-square { display: block; }
  .card-front .brand-lockup { top: 176px; font-size: 30px; color: var(--foil); }
  .card-front .brand-square { width: 34px; height: 34px; background: var(--foil); }
  .card-back .brand-lockup { top: 72px; font-size: 24px; color: var(--brand-red); }
  .card-back .brand-square { width: 28px; height: 28px; background: var(--brand-red); }

  .holder {
    position: absolute;
    right: 380px;
    top: 212px;
    text-align: right;
  }
  .holder-name { font-size: 34px; line-height: 1; white-space: nowrap; }
  .holder-name .first { font-weight: 700; color: var(--brand-red); }
  .holder-name .last { font-weight: 400; color: var(--brand-cyan); }
  .holder-title { font-size: 18px; color: var(--ink); margin-top: 8px; }

  .divider {
    position: absolute;
    left: 350px; top: 195px;
    width: 2px; height: 119px;
    background: var(--brand-red);
  }

  .contact-list {
    position: absolute;
    left: 384px; top: 206px;
    list-style: none;
  }
  .contact-list li {
    display: flex; align-items: center;
    height: 23.5px;
    font-size: 18.5px; color: var(--ink);
    white-space: nowrap;
  }
  .contact-list svg { width: 17px; height: 17px; margin-right: 10px; flex: none; }

  .footer-band { position: absolute; left: 0; top: 0; }
  .address {
    position: absolute; left: 0; right: 0; top: 348px;
    text-align: center; color: var(--paper); font-size: 17.5px;
  }
</style>
</head>
<body>
  <section class="card card-front">
    <div class="brand-lockup"><span class="brand-square"></span><span>Veldmark Supplies</span></div>
  </section>

  <section class="card card-back">
    <div class="brand-lockup"><span class="brand-square"></span><span>Veldmark Supplies</span></div>

    <svg class="footer-band" width="702" height="400" viewBox="0 0 702 400">
      <path d="M0 283 Q351 393 702 283 L702 400 L0 400 Z" fill="var(--brand-red)"/>
      <path d="M25 283 Q351 387 677 283 Q351 376 25 283 Z" fill="var(--brand-cyan)"/>
    </svg>

    <div class="holder">
      <p class="holder-name"><span class="first">Mirela</span> <span class="last">Kostova</span></p>
      <p class="holder-title">Co-Founder &amp; CEO</p>
    </div>

    <div class="divider"></div>

    <ul class="contact-list">
      <li><svg viewBox="0 0 24 24"><path d="M6 3l3 0 1.5 5-2 1.5c1 2.2 2.8 4 5 5L15 12.5l5 1.5v3c0 1.2-1 2-2.2 2C10 18.5 5.5 14 5 6.2 5 4 5.5 3 6 3z" fill="var(--brand-cyan)"/></svg>(817) 555-0142</li>
      <li><svg viewBox="0 0 24 24"><rect x="7" y="2" width="10" height="20" rx="2" fill="none" stroke="var(--brand-red)" stroke-width="2"/></svg>(555) 010-4821</li>
      <li><svg viewBox="0 0 24 24"><circle cx="12" cy="12" r="10" fill="var(--brand-cyan)"/><path d="M4 10c3 0 4 2 6 2s1 4 3 5M14 3c0 3 3 3 3 6s3 2 5 2" stroke="#fff" stroke-width="1.6" fill="none"/></svg>www.veldmark.com</li>
      <li><svg viewBox="0 0 24 24"><rect x="2" y="7" width="20" height="14" fill="var(--brand-red)"/><path d="M2 7l10 8 10-8" stroke="#fff" stroke-width="1.6" fill="none"/><circle cx="12" cy="6" r="3.5" fill="none" stroke="var(--brand-red)" stroke-width="1.6"/></svg>info@veldmark.com</li>
    </ul>

    <p class="address">1840 Lindell Ave. Suite 300 Fort Worth, TX 76107</p>
  </section>
</body>
</html>
```